Exciting Clear Cup Design!

We are a thriving breakfast, lunch and pastry shop that encourages our guests to drink water instead of soda, and wanted to find a way to add value by giving our guests a clear disposable yet reuseable cup with water, instead of the glassware we are currently using. We want them to be able to take the cup with them.
I would like to include a maybe a character or a drawing of water or a cup full of water.
I really like the verandoro bags, and I often save the clear cups from brimwell that are technically disposable but nice to have at my desk as a refillable water cup with a lid. Check out our website, TovarisCafe.example, so you can see our brand. We are locally owned, a busy mom and pop cafe, and want the design to include our logo as well as something cool or cute or catchy.

Target Market(s)

affluent professionals, health conscious people, foodies

Industry/Entity Type

Shop

Requirements
Must have
• our logo
Nice to have
• (just ideas)
a catchy phrase
drink water
one of your 8 glasses

```html
<!DOCTYPE html>
<html lang="en">
<head>
<meta charset="utf-8">
<title>Tovaris – Water Cup Wrap</title>
<link rel="stylesheet" href="https://fonts.googleapis.com/css2?family=Arimo:wght@700&family=Cormorant+Garamond:wght@400;500&family=Pinyon+Script&display=swap">
<style>
  :root {
    --page: #ffffff;
    --wrap-peach: #e8b89c;
    --wrap-peach-light: #efc6ad;
    --motif-tan: #c99a7c;
    --band-brown: #5c3418;
    --band-brown-dark: #4a2810;
    --band-ornament: #8a5a36;
    --logo-olive: #4b3a12;
    --script-ink: #3c2a14;
    --fold-line: #ffffff;
  }
  * { box-sizing: border-box; margin: 0; padding: 0; }
  html, body {
    width: 1200px;
    height: 351px;
    overflow: hidden;
    background: var(--page);
  }
  .canvas {
    position: relative;
    width: 1200px;
    height: 351px;
    background: var(--page);
  }
  .cup-wrap {
    position: absolute;
    left: 50px;
    top: 53px;
    width: 1100px;
    height: 245px;
    background: var(--wrap-peach);
    overflow: hidden;
  }
  .wrap-pattern {
    position: absolute;
    inset: 31px 0;
    background:
      radial-gradient(circle at 12% 30%, rgba(201,154,124,0.35), transparent 9%),
      radial-gradient(circle at 34% 22%, rgba(201,154,124,0.3), transparent 8%),
      radial-gradient(circle at 28% 75%, rgba(201,154,124,0.3), transparent 8%),
      radial-gradient(circle at 66% 30%, rgba(201,154,124,0.3), transparent 8%),
      radial-gradient(circle at 80% 70%, rgba(201,154,124,0.3), transparent 8%),
      radial-gradient(circle at 96% 40%, rgba(201,154,124,0.3), transparent 7%),
      radial-gradient(ellipse at 45% 50%, var(--wrap-peach-light), var(--wrap-peach) 70%);
  }
  .slogan {
    position: absolute;
    font-family: "Arimo", sans-serif;
    font-weight: 700;
    color: var(--motif-tan);
    white-space: nowrap;
    line-height: 1;
  }
  .slogan.s1 { left: 88px;  top: 98px;  font-size: 13px; transform: rotate(4deg); }
  .slogan.s2 { left: 120px; top: 138px; font-size: 21px; transform: rotate(-18deg); }
  .slogan.s3 { left: 160px; top: 188px; font-size: 14px; transform: rotate(14deg); }
  .slogan.s4 { left: 660px; top: 96px;  font-size: 16px; transform: rotate(4deg); }
  .slogan.s5 { left: 870px; top: 50px;  font-size: 14px; transform: rotate(-10deg); }
  .slogan.s6 { left: 800px; top: 188px; font-size: 40px; transform: rotate(10deg); }
  .border-band {
    position: absolute;
    left: 0;
    width: 100%;
    height: 31px;
    background:
      repeating-linear-gradient(90deg, transparent 0 26px, rgba(138,90,54,0.45) 26px 40px, transparent 40px 52px),
      linear-gradient(180deg, var(--band-brown), var(--band-brown-dark));
    z-index: 2;
  }
  .border-band.top { top: 0; }
  .border-band.bottom { bottom: 0; }
  .fold-line {
    position: absolute;
    right: 46px;
    top: 31px;
    bottom: 31px;
    border-left: 2px dashed var(--fold-line);
    opacity: 0.85;
  }
  .brand-lockup {
    position: absolute;
    left: 536px;
    top: 50px;
    transform: translateX(-50%);
    display: flex;
    flex-direction: column;
    align-items: center;
  }
  .brand-dot {
    width: 84px;
    height: 84px;
    border-radius: 50%;
    background: var(--logo-olive);
  }
  .brand-name {
    margin-top: 8px;
    font-family: "Cormorant Garamond", serif;
    font-weight: 500;
    font-size: 60px;
    line-height: 1;
    letter-spacing: 2px;
    color: var(--logo-olive);
  }
  .promise-block {
    position: absolute;
    left: 985px;
    top: 60px;
    transform: translateX(-50%);
    width: 170px;
    text-align: center;
    color: var(--script-ink);
    font-family: "Pinyon Script", cursive;
  }
  .promise-block .headline { font-size: 15px; line-height: 1.15; }
  .promise-block .line { font-size: 12px; line-height: 1.25; }
  .promise-block .rule {
    margin: 6px auto;
    width: 150px;
    height: 1px;
    background: var(--script-ink);
  }
  .promise-block .footnote {
    font-family: "Cormorant Garamond", serif;
    font-size: 8px;
    letter-spacing: 0.5px;
  }
</style>
</head>
<body>
<main class="canvas">
  <section class="cup-wrap">
    <div class="wrap-pattern" role="img" aria-label="Scattered faint pattern of water cups, forks and spoons on a peach wood-grain background"></div>

    <p class="slogan s1">DRINK WATER</p>
    <p class="slogan s2">DRINK WATER</p>
    <p class="slogan s3">DRINK WATER</p>
    <p class="slogan s4">DRINK WATER</p>
    <p class="slogan s5">DRINK WATER</p>
    <p class="slogan s6">DRINK</p>

    <div class="border-band top" role="img" aria-label="Brown border band with swirl and cutlery ornaments"></div>
    <div class="border-band bottom" role="img" aria-label="Brown border band with swirl and cutlery ornaments"></div>
    <div class="fold-line"></div>

    <div class="brand-lockup">
      <div class="brand-dot"></div>
      <div class="brand-name">Tovaris</div>
    </div>

    <div class="promise-block">
      <p class="headline">Fresh From Our Kitchen</p>
      <p class="line">Breakfast, Lunch &amp; Pastry Daily</p>
      <p class="line">Locally Owned &amp; Proudly Served</p>
      <div class="rule"></div>
      <p class="footnote">REFILL ME &amp; DRINK WATER DAILY</p>
    </div>
  </section>
</main>
</body>
</html>
```